I need a business card for my original fine art pieces

I would like a business card design including a logo design for a new business in the art world. I am based in the Hunter Valley NSW Australia. I am a contemporary figurative, encaustic and wildlife artist. I would like to be able to upload my email and mobile number to this as well. This design should be one that I can incorporate into banners and flyers etc. Id like to incorporate one of my own images or partial image into the background or somewhere below. My initials are RJ and I would like these used as a logo type. I would like the use of some colour and it to be bright and catchy. The final design should communicate artwork custom made and commissions available.

Overview: Original Fine Artworks for sale, online, art galleries etc, Custom made to order and by commission.

Target market is world wide audience and corporate world

My figurative work is painted using acrylics in a lot of natural ochre colours that reflect the Australian Outback, on canvas, linen, paper or board: My encaustic work is created in a contemporary abstract style using a blow torch and a made with a medium of 100% pure bees wax, Damar resin, mixed media and coloured pigments, applied to Birch board. My wildlife are created using coloured pencil and mixed media on a variety of paper types or board.

```html
<!DOCTYPE html>
<html lang="en">
<head>
<meta charset="utf-8">
<title>Rhea Jardine – Business Card</title>
<link href="https://fonts.googleapis.com/css2?family=Open+Sans:wght@400;600&display=swap" rel="stylesheet">
<style>
  :root {
    --backdrop: #2b2b2b;
    --card: #0d0d0d;
    --card-panel: #141414;
    --accent: #ff4e0f;
    --text-light: #f2f2f2;
    --text-soft: #d9d9d9;
  }
  * { box-sizing: border-box; margin: 0; padding: 0; }
  html, body { width: 1200px; height: 900px; overflow: hidden; }
  body {
    background: var(--backdrop);
    font-family: "Open Sans", Arial, sans-serif;
    display: flex;
    align-items: center;
    justify-content: center;
    gap: 60px;
  }
  .card {
    width: 525px;
    height: 300px;
    background: var(--card);
    border-radius: 22px;
    position: relative;
    overflow: hidden;
    box-shadow: 0 18px 40px rgba(0,0,0,0.45);
  }

  /* Contact side */
  .card--contact { display: flex; }
  .contact__brand-area {
    width: 46%;
    display: flex;
    align-items: center;
    justify-content: center;
  }
  .contact__details {
    flex: 1;
    background: var(--card-panel);
    padding: 46px 24px 0 30px;
    color: var(--text-light);
  }

  /* Brand name placeholder: plain circle + name in one colour and weight */
  .brand-lockup {
    display: flex;
    align-items: center;
    gap: 10px;
  }
  .brand-lockup__dot {
    border-radius: 50%;
    background: var(--accent);
    flex: none;
  }
  .brand-lockup__name {
    color: var(--accent);
    font-weight: 600;
    letter-spacing: 1px;
    white-space: nowrap;
  }
  .brand-lockup--contact .brand-lockup__dot { width: 16px; height: 16px; }
  .brand-lockup--contact .brand-lockup__name { font-size: 22px; }
  .brand-lockup--back .brand-lockup__dot { width: 20px; height: 20px; }
  .brand-lockup--back .brand-lockup__name { font-size: 28px; }

  .person__name { color: var(--accent); font-size: 19px; font-weight: 400; line-height: 1.2; }
  .person__role { font-size: 14px; color: var(--text-soft); margin-bottom: 16px; }
  .address { font-size: 14px; line-height: 1.4; color: var(--text-soft); margin-bottom: 14px; }
  .contact-list { list-style: none; font-size: 14px; line-height: 1.55; color: var(--text-soft); }
  .contact-list li { display: flex; align-items: center; gap: 9px; }
  .contact-list svg { width: 12px; height: 12px; flex: none; }

  /* Brand side */
  .card--brand {
    display: flex;
    flex-direction: column;
    align-items: center;
    justify-content: center;
  }
  .brand__tagline {
    margin-top: 8px;
    color: var(--text-light);
    font-size: 12.5px;
    font-weight: 600;
    letter-spacing: 2.6px;
  }
</style>
</head>
<body>

<section class="card card--contact" aria-label="Business card, contact side">
  <div class="contact__brand-area">
    <div class="brand-lockup brand-lockup--contact">
      <span class="brand-lockup__dot" aria-hidden="true"></span>
      <span class="brand-lockup__name">Rhea Jardine</span>
    </div>
  </div>
  <div class="contact__details">
    <p class="person__name">Daniel Hughes</p>
    <p class="person__role">Managing Director</p>
    <p class="address">42 Vine Street, Pokolbin<br>NSW Australia, 2320.</p>
    <ul class="contact-list">
      <li>
        <svg viewBox="0 0 24 24" aria-hidden="true"><path fill="#ff4e0f" d="M6.6 10.8a15 15 0 0 0 6.6 6.6l2.2-2.2c.3-.3.7-.4 1-.2 1.1.4 2.3.6 3.6.6.6 0 1 .4 1 1V20c0 .6-.4 1-1 1A17 17 0 0 1 3 4c0-.6.4-1 1-1h3.5c.6 0 1 .4 1 1 0 1.3.2 2.5.6 3.6.1.3 0 .7-.2 1z"/></svg>
        044-987 654 321
      </li>
      <li>
        <svg viewBox="0 0 24 24" aria-hidden="true"><rect x="2" y="5" width="20" height="14" rx="2" fill="#ff4e0f"/><path d="M3 6l9 7 9-7" fill="none" stroke="#141414" stroke-width="2"/></svg>
        hello@rjstudio.com
      </li>
      <li>
        <svg viewBox="0 0 24 24" aria-hidden="true"><g fill="none" stroke="#ff4e0f" stroke-width="3" stroke-linecap="round"><path d="M10 14a4 4 0 0 0 5.7 0l3.6-3.6a4 4 0 0 0-5.7-5.7L12 6.3"/><path d="M14 10a4 4 0 0 0-5.7 0l-3.6 3.6a4 4 0 0 0 5.7 5.7l1.6-1.6"/></g></svg>
        www.rjfineart.com
      </li>
    </ul>
  </div>
</section>

<section class="card card--brand" aria-label="Business card, brand side">
  <div class="brand-lockup brand-lockup--back">
    <span class="brand-lockup__dot" aria-hidden="true"></span>
    <h1 class="brand-lockup__name">RHEA JARDINE</h1>
  </div>
  <p class="brand__tagline">ORIGINAL FINE ARTWORKS</p>
</section>

</body>
</html>
```